Lumen Harbor is a Smart Device and Wiring Business offering the latest in Smart Home Devices inc

Looking for a new website to draw people to my business and explain what a smart home is all about. I currently own a domain and have a website I put together in webquill business website builder. address www.lumenharbor.example. The website needs modernising and be visually appealing with cool action buttons, client feedback page etc.

The webpage needs to present an image of seamless integration of wireless voice control and smart devices that take tasks and activities away from the owner saving them time and money.

I have a facebook business page(lumen harbor) and instagram linked with the business, are we able to link this to the website somehow?

Target Market(s)

Residential home owners who want to modernise their home. Who have seen adverts for corvo hub and pellar mira and want to put it in their home.

Industry/Entity Type

Technology Equipment

Number of Pages Required

1 page

Colors

Designer to choose colors to be used in the design.

Requirements
Must have
• A great landing page, that is modern and attractive, that gets across the idea of smart devices and technology.
• Must be ios/android device friendly.
Nice to have
• interactive/animated buttons
• I like the direction and interactiveness of these websites, a simplified version would be awesome.
• Something in between:
• http://www.quorbeliving.example/ and https://plindo.example/
• http://www.quorbeliving.example/

```html
<!DOCTYPE html>
<html lang="en">
<head>
<meta charset="utf-8">
<title>Lumen Harbor – Smart Device Integration</title>
<link rel="stylesheet" href="https://fonts.googleapis.com/css2?family=Lato:wght@400;700;900&family=Oswald:wght@400;500&display=swap">
<style>
:root{
  --blue:#1e6fb8;
  --blue-dark:#155a98;
  --cyan:#17b3e6;
  --ink:#222a33;
  --text:#5b6470;
  --muted:#8a929c;
  --line:#d5dbe2;
  --white:#ffffff;
  --topbar:#1d6db6;
  --dark:#2a2e33;
  --footer:#1b1e22;
}
*{box-sizing:border-box;margin:0;padding:0}
html,body{width:1200px;height:4128px;overflow:hidden;background:var(--white)}
body{font-family:"Lato",sans-serif;color:var(--text);position:relative}
.abs{position:absolute}
.page{position:relative;width:1200px;height:4128px;overflow:hidden}

/* top bar */
.topbar{left:0;top:0;width:1200px;height:50px;background:var(--topbar);color:var(--white);font-size:15px}
.topbar .social{top:16px;width:18px;height:18px;border-radius:50%;background:var(--white)}
.topbar .contact{top:15px;display:flex;align-items:center;gap:10px}
.topbar .chip{width:22px;height:22px;border-radius:50%;background:var(--white);display:flex;align-items:center;justify-content:center}

/* header */
.header{left:0;top:50px;width:1200px;height:110px;background:var(--white)}
.brand{display:flex;align-items:center;gap:14px}
.brand-mark{width:62px;height:62px;border-radius:50%;background:var(--blue)}
.brand-name{font-family:"Lato",sans-serif;font-weight:900;font-size:34px;letter-spacing:2px;color:var(--ink);line-height:1}
.nav a{position:absolute;top:47px;font-size:15px;color:var(--ink);text-decoration:none}
.nav a.active{color:var(--blue)}

/* hero */
.hero{left:0;top:160px;width:1200px;height:600px;background:linear-gradient(135deg,#3a3f44 0%,#5d6166 45%,#2b2f33 100%)}
.hero-title{left:0;width:1200px;top:150px;text-align:center;color:var(--white);font-weight:900;font-size:38px;letter-spacing:2px}
.hero-sub{left:0;width:1200px;top:207px;text-align:center;color:var(--cyan);font-weight:900;font-size:42px;letter-spacing:2px}
.hero-lead{left:0;width:1200px;top:272px;text-align:center;color:var(--white);font-weight:700;font-size:24px;line-height:34px}
.arrow{width:62px;height:62px;border-radius:50%;display:flex;align-items:center;justify-content:center}
.arrow.prev{left:46px;top:269px;background:var(--white)}
.arrow.next{left:1089px;top:269px;background:var(--cyan)}

/* steps */
.step{width:260px;text-align:center}
.step-icon{width:112px;height:112px;border-radius:50%;background:var(--blue);border:6px solid var(--white);box-shadow:0 0 0 3px var(--blue);margin:0 auto;display:flex;align-items:center;justify-content:center}
.step h3{font-size:21px;font-weight:700;color:var(--cyan);margin-top:14px}
.step p{font-size:14px;line-height:22px;color:var(--text);margin-top:10px;padding:0 30px}
.step p a,.card p a{color:var(--blue-dark);text-decoration:underline}

/* section heads */
.section-head{font-family:"Oswald",sans-serif;font-weight:500;text-transform:uppercase}
.what-head{left:0;width:1200px;top:977px;text-align:center;font-size:40px;color:var(--blue-dark);display:flex;justify-content:center;align-items:center;gap:26px}
.what-head span.rule{width:90px;height:1px;background:var(--line)}
.product-frame{left:358px;top:1060px;width:482px;height:302px;border-radius:28px;background:var(--white);box-shadow:0 4px 24px rgba(0,0,0,.14);overflow:hidden}
.product-frame .fill{position:absolute;left:40px;top:30px;right:40px;bottom:30px;border-radius:18px;background:linear-gradient(90deg,#3b3f45,#d9dcdf 40%,#eceef0 60%,#2f3338)}
.what-text{left:150px;width:900px;top:1393px;text-align:center;font-size:15px;line-height:26px;color:var(--text)}
.btn{display:flex;align-items:center;justify-content:center;color:var(--white);text-transform:uppercase;border-radius:40px;font-weight:700}
.btn-contact{left:517px;top:1467px;width:166px;height:64px;background:var(--cyan);font-size:17px}

/* welcome */
.welcome{left:0;top:1615px;width:1200px;height:455px;background:linear-gradient(90deg,#26292d 0%,#3c3f43 60%,#55585c 100%)}
.welcome h2{left:80px;top:50px;font-size:46px;color:var(--white)}
.welcome p{left:80px;top:130px;width:580px;font-size:14.5px;line-height:24px;color:var(--white)}
.btn-more{left:77px;top:342px;width:138px;height:54px;background:var(--blue);font-size:13px}
.welcome-photo{left:737px;top:61px;width:336px;height:336px;border-radius:50%;border:5px solid var(--cyan);background:radial-gradient(circle at 50% 45%,#8a6a4e,#4b3a2c 60%,#2a211a)}

/* specialists */
.spec-head{left:0;width:1200px;top:2122px;text-align:center;font-size:44px;color:var(--ink)}
.spec-head b{color:var(--blue);font-weight:500}
.card{width:322px;text-align:center}
.card .photo{height:204px;border-bottom:6px solid var(--blue)}
.card h4{font-size:19px;font-weight:700;color:var(--blue-dark);margin-top:24px}
.card p{font-size:14.5px;line-height:26px;margin-top:6px;padding:0 14px}
.sq{width:42px;height:42px;background:var(--blue);display:flex;align-items:center;justify-content:center}

/* products */
.products{left:0;top:2592px;width:1200px;height:375px;background:linear-gradient(90deg,#1c5e9d,#2f7cc1 55%,#3b86c6)}
.products h2{left:80px;top:50px;font-size:44px;color:var(--white)}
.products p.lead{left:80px;top:122px;width:380px;font-size:14.5px;line-height:24px;color:var(--white)}
.pkg{width:200px;text-align:center;color:var(--white)}
.pkg .ring{width:100px;height:100px;border-radius:50%;background:var(--white);border:4px solid #bfe3f6;margin:0 auto;display:flex;align-items:center;justify-content:center;color:var(--blue);font-size:15px;line-height:19px}
.pkg p{font-size:14.5px;line-height:24px;margin-top:28px}

/* testimonials */
.testimonials{left:0;top:2967px;width:1200px;height:344px;background:linear-gradient(90deg,#1d1f22,#35383c 50%,#24262a)}
.testimonials h2{left:0;width:1200px;top:42px;text-align:center;font-size:44px;color:var(--white)}
.avatar{left:190px;top:126px;width:116px;height:116px;border-radius:50%;background:linear-gradient(#d9c2ad,#9d7b62);border:3px solid var(--white)}
.quote{left:350px;top:138px;width:780px;font-size:14.5px;line-height:24px;color:var(--white)}
.quote strong{display:block;margin-top:2px}
.dots{left:566px;top:262px;display:flex;gap:10px}
.dots span{width:14px;height:14px;border-radius:50%;border:2px solid var(--white)}
.dots span.on{background:var(--white)}

/* contact */
.contact-head{left:80px;top:3372px;font-size:46px;color:var(--ink)}
.contact-head b{color:var(--blue);font-weight:500}
.field{border:1.5px solid var(--line);border-radius:26px;height:50px;padding:15px 18px;font-size:14px;color:var(--muted)}
.field.msg{height:105px;border-radius:20px}
.btn-submit{left:77px;top:3699px;width:655px;height:50px;background:var(--blue);font-size:14px}
.info{left:797px;display:flex;align-items:flex-start;gap:22px;font-size:15px;line-height:24px;color:var(--text);width:300px}
.info svg{flex:none;margin-top:4px}

/* footer */
.footer{left:0;top:3812px;width:1200px;height:316px;background:linear-gradient(180deg,#26292d,#17191c)}
.footer .brand{left:0;width:1200px;top:52px;justify-content:center}
.footer .brand-mark{background:var(--white)}
.footer .brand-name{color:var(--white)}
.footer-nav{left:0;width:1200px;top:143px;display:flex;justify-content:center;gap:22px;font-size:15px;color:var(--white)}
.footer-social{left:0;width:1200px;top:190px;display:flex;justify-content:center;gap:18px}
.footer-social span{width:38px;height:38px;border-radius:50%;background:var(--white)}
.footer-rule{left:77px;width:1046px;top:248px;height:1px;background:#4d5258}
.copyright{left:0;width:1200px;top:274px;text-align:center;font-size:14px;color:var(--white)}
</style>
</head>
<body>
<div class="page">

  <!-- top bar -->
  <div class="abs topbar">
    <span class="abs social" style="left:74px"></span>
    <span class="abs social" style="left:107px"></span>
    <span class="abs social" style="left:142px"></span>
    <div class="abs contact" style="left:708px">
      <span class="chip"><svg width="12" height="12" viewBox="0 0 24 24"><path fill="#1d6db6" d="M6.6 10.8a15 15 0 0 0 6.6 6.6l2.2-2.2a1 1 0 0 1 1-.25 11.4 11.4 0 0 0 3.6.57 1 1 0 0 1 1 1V20a1 1 0 0 1-1 1A17 17 0 0 1 3 4a1 1 0 0 1 1-1h3.5a1 1 0 0 1 1 1c0 1.25.2 2.45.57 3.6a1 1 0 0 1-.25 1z"/></svg></span>
      <span>0400 555 019</span>
    </div>
    <div class="abs contact" style="left:895px">
      <span class="chip"><svg width="12" height="12" viewBox="0 0 24 24"><path fill="#1d6db6" d="M2 5h20v14H2z M2 5l10 8 10-8" stroke="#fff" stroke-width="1.5"/></svg></span>
      <span>info@lumenharbor.example</span>
    </div>
  </div>

  <!-- header -->
  <header class="abs header">
    <div class="abs brand" style="left:77px;top:24px">
      <span class="brand-mark"></span>
      <span class="brand-name">LUMEN HARBOR</span>
    </div>
    <nav class="nav">
      <a class="active" style="left:563px">Home</a>
      <a style="left:660px">About Us</a>
      <a style="left:779px">What We Do</a>
      <a style="left:920px">Products</a>
      <a style="left:1040px">Contact Us</a>
    </nav>
  </header>

  <!-- hero -->
  <section class="abs hero" role="img" aria-label="Photo of a modern living room with a wall-mounted television, fireplace and tall speakers">
    <h1 class="abs hero-title">LUMEN HARBOR</h1>
    <div class="abs hero-sub">SMART DEVICE INTEGRATION</div>
    <p class="abs hero-lead">We are focused on delivering affordable and easily usable devices<br>for your home and office.</p>
    <div class="abs arrow prev"><svg width="26" height="16" viewBox="0 0 26 16"><path d="M25 8H3M9 2 2 8l7 6" fill="none" stroke="#555" stroke-width="2"/></svg></div>
    <div class="abs arrow next"><svg width="26" height="16" viewBox="0 0 26 16"><path d="M1 8h22M17 2l7 6-7 6" fill="none" stroke="#fff" stroke-width="2"/></svg></div>
  </section>
  <svg class="abs" style="left:0;top:600px" width="1200" height="170" viewBox="0 0 1200 170" aria-hidden="true">
    <path d="M0 170 L0 150 Q600 -10 1200 150 L1200 170 Z" fill="#fff"/>
  </svg>

  <!-- steps -->
  <div class="abs step" style="left:79px;top:687px">
    <div class="step-icon"><svg width="52" height="52" viewBox="0 0 52 52" fill="none" stroke="#fff" stroke-width="3"><rect x="18" y="4" width="16" height="12" rx="2"/><rect x="4" y="34" width="14" height="12" rx="2"/><rect x="34" y="34" width="14" height="12" rx="2"/><path d="M26 16v9M11 34v-9h30v9"/></svg></div>
    <h3>Consultation</h3>
    <p>We meet to discuss your vision, gather requirements, and properly...<a>READ MORE</a></p>
  </div>
  <div class="abs step" style="left:338px;top:654px">
    <div class="step-icon"><svg width="52" height="52" viewBox="0 0 52 52" fill="none" stroke="#fff" stroke-width="3"><circle cx="26" cy="26" r="20"/><path d="M16 16l20 20M36 16 16 36"/></svg></div>
    <h3>Installation</h3>
    <p>Upon acceptance of project document we build your system...<a>READ MORE</a></p>
  </div>
  <div class="abs step" style="left:599px;top:654px">
    <div class="step-icon"><svg width="52" height="52" viewBox="0 0 52 52" fill="none" stroke="#fff" stroke-width="3"><rect x="11" y="6" width="30" height="40" rx="2"/><path d="M17 18l3 3 5-6M29 18h7M17 30l3 3 5-6M29 30h7"/></svg></div>
    <h3>Finalisation</h3>
    <p>After installing the product we run you through your system...<a>READ MORE</a></p>
  </div>
  <div class="abs step" style="left:855px;top:687px">
    <div class="step-icon"><svg width="52" height="52" viewBox="0 0 52 52" fill="none" stroke="#fff" stroke-width="3"><path d="M10 28a16 16 0 0 1 32 0"/><rect x="6" y="26" width="8" height="12" rx="2"/><rect x="38" y="26" width="8" height="12" rx="2"/><path d="M42 38q0 8-12 8"/></svg></div>
    <h3>Support</h3>
    <p>We offer tech support when difficulties arise, making sure that your...<a>READ MORE</a></p>
  </div>

  <!-- what we do -->
  <h2 class="abs section-head what-head"><span class="rule"></span>What We Do<span class="rule"></span></h2>
  <div class="abs product-frame"><div class="fill" role="img" aria-label="Product shot of a group of smart speakers and voice assistants"></div></div>
  <p class="abs what-text">We are a small group of Perth Tech consultants, with long-term experience in the integration, setup and fault finding of advanced technologies, we are passionate about the products we sell and confident in the service we provide.</p>
  <div class="abs btn btn-contact">Contact Us</div>

  <!-- welcome -->
  <section class="abs welcome" role="img" aria-label="Background photo of people at home using a tablet">
    <h2 class="abs section-head">Welcome to Lumen Harbor</h2>
    <p class="abs">Lorem Ipsum is simply dummy text of the printing and typesetting industry. Lorem Ipsum has been the industry's standard dummy text ever since the 1500s, when an unknown printer took a galley of type and scrambled it to make a type specimen book. It has survived not only five centuries, but also the leap into typesetting, remaining essentially unchanged. It was popularised in the 1960s with the release of Typorama sheets containing Lorem Ipsum passages, and with desktop publishing software like Quillset Layout including versions of Lorem Ipsum.</p>
    <div class="abs btn btn-more">Know More</div>
    <div class="abs welcome-photo" role="img" aria-label="Hands operating a home control app on a tablet"></div>
  </section>

  <!-- specialists -->
  <h2 class="abs section-head spec-head">Smart <b>Home Specialists</b></h2>
  <div class="abs sq" style="left:19px;top:2353px"><svg width="18" height="14" viewBox="0 0 18 14" fill="none" stroke="#fff" stroke-width="2"><path d="M8 1 2 7l6 6M16 1l-6 6 6 6"/></svg></div>
  <div class="abs sq" style="left:1139px;top:2353px"><svg width="18" height="14" viewBox="0 0 18 14" fill="none" stroke="#fff" stroke-width="2"><path d="M2 1l6 6-6 6M10 1l6 6-6 6"/></svg></div>
  <div class="abs card" style="left:77px;top:2218px">
    <div class="photo" role="img" aria-label="Hand holding a remote in an automated living room" style="background:linear-gradient(135deg,#e9ecef,#b8bfc7 60%,#7d858e)"></div>
    <h4>Home Automation</h4>
    <p>Your own concierge in a box, control your home devices, lights and...<a>Read More</a></p>
  </div>
  <div class="abs card" style="left:440px;top:2218px">
    <div class="photo" role="img" aria-label="Voice assistant speaker on a table" style="background:linear-gradient(135deg,#5d6a78,#2b3038 60%,#8c96a2)"></div>
    <h4>Voice Control With Mira</h4>
    <p>Your own concierge in a box, control your home devices, lights and...<a>Read More</a></p>
  </div>
  <div class="abs card" style="left:800px;top:2218px">
    <div class="photo" role="img" aria-label="Hand holding a phone next to a smart door lock" style="background:linear-gradient(135deg,#6b4e36,#3a2a1e 55%,#9a9ea3)"></div>
    <h4>Keyless Entry</h4>
    <p>Your own concierge in a box, control your home devices, lights and...<a>Read More</a></p>
  </div>

  <!-- products -->
  <section class="abs products" role="img" aria-label="Blue tinted background photo of a hand using a touch screen">
    <h2 class="abs section-head">Our Products</h2>
    <p class="abs lead">Lorem Ipsum is simply dummy text of the printing and typesetting industry. Lorem Ipsum has been the industry's standard dummy text ever since the 1500s, when an unknown printer took a galley of type and scrambled it to make a type specimen book. It has survived not only five centuries, but also the leap into electronic typesetting, remaining essentially unchanged.</p>
    <div class="abs pkg" style="left:533px;top:118px"><div class="ring">Silver<br>Package</div><p>The Silver Package gives you the foundation of a Smart...</p></div>
    <div class="abs pkg" style="left:731px;top:118px"><div class="ring">Gold<br>Package</div><p>The Gold package takes the foundation of the Silver...</p></div>
    <div class="abs pkg" style="left:929px;top:118px"><div class="ring">Platinum<br>Package</div><p>The Platinum Package has all the bells and whistles...</p></div>
  </section>

  <!-- testimonials -->
  <section class="abs testimonials" role="img" aria-label="Dark background photo of a hand pointing at a wall control panel">
    <h2 class="abs section-head">Testimonials</h2>
    <div class="abs avatar" role="img" aria-label="Client portrait"></div>
    <p class="abs quote">Lorem Ipsum is simply dummy text of the printing and typesetting industry. Lorem Ipsum has been the industry's standard dummy text ever since the 1500s, when an unknown printer took a galley of type and scrambled it to make a type specimen book. It has survived not only five centuries.<strong>- CLIENT NAME</strong></p>
    <div class="abs dots"><span class="on"></span><span></span><span></span></div>
  </section>

  <!-- contact -->
  <h2 class="abs section-head contact-head">Contact <b>Us</b></h2>
  <div class="abs field" style="left:77px;top:3462px;width:322px">Name*</div>
  <div class="abs field" style="left:410px;top:3462px;width:322px">E-mail*</div>
  <div class="abs field" style="left:77px;top:3523px;width:322px">Phone*</div>
  <div class="abs field" style="left:410px;top:3523px;width:322px">Subject</div>
  <div class="abs field msg" style="left:77px;top:3583px;width:655px">Message</div>
  <div class="abs btn btn-submit">Submit</div>
  <div class="abs info" style="top:3535px"><svg width="16" height="20" viewBox="0 0 16 20"><path fill="#1e6fb8" d="M8 0a8 8 0 0 1 8 8c0 6-8 12-8 12S0 14 0 8a8 8 0 0 1 8-8zm0 5a3 3 0 1 0 0 6 3 3 0 0 0 0-6z"/></svg><span>123,Lorem Ipsum is simply dummy text of the printing</span></div>
  <div class="abs info" style="top:3611px"><svg width="16" height="16" viewBox="0 0 24 24"><path fill="#1e6fb8" d="M6.6 10.8a15 15 0 0 0 6.6 6.6l2.2-2.2a1 1 0 0 1 1-.25 11.4 11.4 0 0 0 3.6.57 1 1 0 0 1 1 1V20a1 1 0 0 1-1 1A17 17 0 0 1 3 4a1 1 0 0 1 1-1h3.5a1 1 0 0 1 1 1c0 1.25.2 2.45.57 3.6a1 1 0 0 1-.25 1z"/></svg><span>0400 555 019</span></div>
  <div class="abs info" style="top:3660px"><svg width="18" height="14" viewBox="0 0 18 14"><rect width="18" height="14" rx="1" fill="#1e6fb8"/><path d="M1 1l8 6 8-6" fill="none" stroke="#fff" stroke-width="1.5"/></svg><span>info@lumenharbor.example</span></div>

  <!-- footer -->
  <footer class="abs footer">
    <div class="abs brand"><span class="brand-mark"></span><span class="brand-name">LUMEN HARBOR</span></div>
    <nav class="abs footer-nav"><span>Home</span><span>|</span><span>About Us</span><span>|</span><span>What We Do</span><span>|</span><span>Products</span><span>|</span><span>Contact Us</span></nav>
    <div class="abs footer-social"><span></span><span></span><span></span></div>
    <div class="abs footer-rule"></div>
    <p class="abs copyright">© LUMEN HARBOR - 2018. All Rights Reserved.</p>
  </footer>

</div>
</body>
</html>
```